Automotive component supplier needs a business card design

We need a business card design for our company called Velran Global Components Ltd based in the UK. We are a supplier of interior and exterior components to premium car manufacturers such as Corvel Ashby, Hadley Fenn, Marquist and Tavarelli. We would like to see a modern business card design that uses the colour blue.

Target Market(s)

Premium automotive car manufacturers.

Industry/Entity Type

Automotive

Contact Information for Business Card

Company Name : Velran Global Components Limited
Address: 17 Marlow Yard, Upper Heath, Warwick, CV31 8QL, United Kingdom
Web Address : www.velrancomponents-example.co.uk

Font styles to use
Other font styles liked:
• Helvetica

Colors
3176b5
0255a3
85acd3
cfdeed
cee9f5
85cae6
34a6d7
0692cd
9bcb3c

Requirements
Must have
• Clear company logo and a mixture of blue colours.
Nice to have
• A high quality modern image.
Should not have
• Multiple colours.

```html
<!DOCTYPE html>
<html lang="en">
<head>
<meta charset="utf-8">
<title>Velran Global Components – Business Card</title>
<link rel="stylesheet" href="https://fonts.googleapis.com/css2?family=Arimo:wght@400;700&display=swap">
<style>
  :root {
    --backdrop: #e4e6e8;
    --card-white: #ffffff;
    --brand-blue: #0692cd;
    --line-blue: #85cae6;
    --pill-blue: #34a6d7;
    --accent-green: #9bcb3c;
    --text-grey: #6b6f73;
    --divider-grey: #cfd3d6;
  }
  * { margin: 0; padding: 0; box-sizing: border-box; }
  html, body {
    width: 1200px; height: 950px; overflow: hidden;
    background: var(--backdrop);
    font-family: "Arimo", Helvetica, Arial, sans-serif;
  }
  .canvas {
    position: relative; width: 1200px; height: 950px;
    display: flex; flex-direction: column; align-items: center; justify-content: center; gap: 50px;
  }
  .card {
    position: relative; width: 700px; height: 400px;
    box-shadow: 0 6px 18px rgba(0,0,0,0.12);
    overflow: hidden;
  }
  .card-front { background: var(--card-white); }
  .card-back { background: var(--accent-green); display: flex; align-items: center; justify-content: center; }

  .brand-name {
    font-weight: 700; color: var(--brand-blue);
    text-transform: uppercase; line-height: 1;
  }
  .brand-name .brand-main { display: block; font-size: 68px; letter-spacing: 2px; }
  .brand-name .brand-sub { display: block; font-size: 19px; letter-spacing: 3px; margin-top: 8px; }

  .card-front .brand-name { position: absolute; top: 60px; right: 60px; text-align: right; }
  .card-back .brand-name { color: var(--card-white); text-align: center; }
  .card-back .brand-name .brand-main { font-size: 110px; letter-spacing: 4px; }
  .card-back .brand-name .brand-sub { font-size: 28px; letter-spacing: 5px; margin-top: 12px; }

  .holder { position: absolute; left: 44px; top: 200px; }
  .holder-name { font-size: 22px; font-weight: 700; color: var(--brand-blue); letter-spacing: 0.5px; }
  .holder-title { font-size: 16px; color: var(--accent-green); margin-top: 6px; }

  .contact { position: absolute; left: 250px; top: 190px; font-size: 14px; color: var(--text-grey); line-height: 1.45; }
  .contact-divider { width: 90px; height: 1px; background: var(--divider-grey); margin: 10px 0; }
  .contact-label { color: var(--brand-blue); font-weight: 700; display: inline-block; width: 22px; }

  .rule-line { position: absolute; left: 0; right: 0; top: 344px; height: 2px; background: var(--line-blue); }
  .web-pill {
    position: absolute; left: 250px; top: 330px; height: 30px; padding: 0 22px;
    background: var(--pill-blue); color: var(--card-white); border-radius: 15px;
    font-size: 14px; line-height: 30px; letter-spacing: 0.3px;
  }
</style>
</head>
<body>
<main class="canvas">
  <section class="card card-front">
    <div class="brand-name"><span class="brand-main">Velran</span><span class="brand-sub">Global Components</span></div>
    <div class="holder">
      <p class="holder-name">ELIAS MORROW</p>
      <p class="holder-title">President</p>
    </div>
    <div class="contact">
      <p>17 Marlow Yard, Upper Heath</p>
      <p>Warwick, CV31 8QL</p>
      <p>United Kingdom</p>
      <div class="contact-divider"></div>
      <p><span class="contact-label">P :</span>512 4098 7731</p>
      <p><span class="contact-label">M :</span>840 2617 9046</p>
      <p><span class="contact-label">E :</span>elias@velrancomponents-example.co.uk</p>
    </div>
    <div class="rule-line"></div>
    <div class="web-pill">www.velrancomponents-example.co.uk</div>
  </section>

  <section class="card card-back">
    <div class="brand-name"><span class="brand-main">Velran</span><span class="brand-sub">Global Components</span></div>
  </section>
</main>
</body>
</html>
```